Satchel & Sundial needs new business card design

I need a new business card design. I'm looking for out-of-the-box design which represents the freedom of being a location independent entrepreneur.
I offer coaching, retreats and trips.
I would like to see designs with and without the photo.
Colors I use are black (#000000), green (#25A796) and brown (#D7C38C)
Website satchelandsundial.example

Target Market(s)

location independent entrepreneurs, digital nomads, people looking to swap the 9 to 5 for a lifestyle business

Industry/Entity Type

Business

Contact Information for Business Card

Dorota Falkner
Your Lifestyle Business Coach, Retreat & Trip Leader
http://satchelandsundial.example
hello@satchelandsundial.example
Live a life you don't need a holiday from

Font styles to use
Serif
Sans Serif

Requirements
Must have
• One side should contain only the logo. I would also consider having the "Live a life you don't need a holiday from" on that side too (depending on how it looks)
• Please show both sides on the designs.

```html
<!DOCTYPE html>
<html lang="en">
<head>
<meta charset="utf-8">
<title>Satchel &amp; Sundial — Business Card</title>
<link href="https://fonts.googleapis.com/css2?family=Source+Sans+3:ital,wght@0,400;0,600;0,700;1,700&display=swap" rel="stylesheet">
<style>
  :root {
    --ink: #000000;
    --teal: #25a796;
    --teal-card: #26a996;
    --paper: #ffffff;
    --soft-white: #f2f2f2;
    --tag-grey: #d9d9d9;
  }
  html, body {
    margin: 0;
    padding: 0;
    width: 1200px;
    height: 900px;
    overflow: hidden;
    background: var(--paper);
    font-family: "Source Sans 3", "Myriad Pro", Arial, sans-serif;
  }
  .canvas {
    position: relative;
    width: 1200px;
    height: 900px;
  }
  .card {
    position: absolute;
    top: 275px;
    width: 477px;
    height: 294px;
    overflow: hidden;
  }
  .card--front {
    left: 116px;
    background: var(--ink);
    border-radius: 0 50px 0 50px;
    color: var(--soft-white);
  }
  .card--back {
    left: 622px;
    background: var(--teal-card);
    border-radius: 50px 0 50px 0;
  }
  .brand-name {
    position: absolute;
    margin: 0;
    color: var(--paper);
    font-weight: 600;
    white-space: nowrap;
    letter-spacing: 0.5px;
  }
  .card--front .brand-name {
    right: 28px;
    top: 56px;
    font-size: 25px;
  }
  .card--back .brand-name {
    left: 0;
    right: 0;
    top: 118px;
    text-align: center;
    font-size: 40px;
  }
  .person {
    position: absolute;
    left: 31px;
    top: 91px;
  }
  .person__name {
    margin: 0 0 2px;
    color: var(--teal);
    font-weight: 700;
    font-size: 18px;
    line-height: 22px;
  }
  .person__role {
    margin: 0;
    font-size: 13.5px;
    line-height: 17px;
    color: var(--soft-white);
  }
  .divider {
    position: absolute;
    left: 0;
    right: 0;
    top: 163px;
    height: 1.5px;
    background: var(--soft-white);
  }
  .contacts {
    position: absolute;
    right: 27px;
    top: 187px;
    margin: 0;
    padding: 0;
    list-style: none;
    text-align: right;
    font-size: 13.5px;
    line-height: 19px;
  }
  .contacts li {
    display: flex;
    align-items: center;
    justify-content: flex-end;
    gap: 5px;
  }
  .contacts svg {
    width: 9px;
    height: 9px;
    flex: none;
  }
  .tagline {
    position: absolute;
    left: 0;
    right: 0;
    top: 245px;
    margin: 0;
    text-align: center;
    font-style: italic;
    font-weight: 700;
    font-size: 14.5px;
    letter-spacing: 2px;
    color: var(--tag-grey);
  }
  .pattern-field {
    position: absolute;
    inset: 0;
    background: var(--teal-card);
  }
</style>
</head>
<body>
<main class="canvas">

  <section class="card card--front" aria-label="Card front">
    <p class="brand-name">Satchel &amp; Sundial</p>

    <div class="person">
      <p class="person__name">Dorota Falkner</p>
      <p class="person__role">Your Lifestyle Business Coach,<br>Retreat &amp; Trip Leader</p>
    </div>

    <div class="divider"></div>

    <ul class="contacts">
      <li>hello@satchelandsundial.example
        <svg viewBox="0 0 10 10" aria-hidden="true">
          <rect x="0" y="1.5" width="10" height="7" fill="var(--teal)"/>
          <polyline points="0.5,2 5,5.5 9.5,2" fill="none" stroke="var(--ink)" stroke-width="1"/>
        </svg>
      </li>
      <li>www.satchelandsundial.example
        <svg viewBox="0 0 10 10" aria-hidden="true">
          <circle cx="5" cy="5" r="4.6" fill="var(--teal)"/>
          <path d="M5 0.6v8.8M0.6 5h8.8" stroke="var(--ink)" stroke-width="0.8"/>
        </svg>
      </li>
    </ul>

    <p class="tagline">LIVE A LIFE YOU DON'T NEED A HOLIDAY FROM</p>
  </section>

  <section class="card card--back" aria-label="Card back">
    <div class="pattern-field" role="img" aria-label="Faint repeating brand-name pattern in darker teal"></div>
    <p class="brand-name">Satchel &amp; Sundial</p>
  </section>

</main>
</body>
</html>
```